Moxy Fen needs some awesome stationary

Do you have what it takes to get my brand? You either do or you don't, have a crack at a design and you my just win my business.

I don't want to waste your or my time, so put your creative genius on either a business card or envelope.

I however need a package of stationary that follows the same brand. I will message you to complete the remaining should I like your first submission.

Here is what I need, have a go!

Basically I need the following for my small business based in melbourne.
- Letterhead (printer ready and MS Word)
- Business Card
- Compliments Slip
- Envelope
- Proposal Cover Page (MS Word only)
- Presentation Folder
- Marbled Fox Cards
- Student Name Tent
- Index Cards
- Vell-Ka

I am establishing the brand and it must be modern, professional but also relaxed; that is not formal and not corporate. It represents a company are leaders, but small enough to care and operate like a bunch of friends. We are bringing people and conversations back to business, and turfing out all the bureaucracy and crazy and wasteful procedures. Its about "lets talk and figure it out together and find even better ways".

Target Market(s)

Mainly companies that build software products, but Agile practices are used in many other industries (even graphic design projects)

Industry/Entity Type

Information Technology

Font styles to use
Sans Serif

Colors
3176b5
aaaaaa

Requirements
Must have
• I like curves and circles and not boxes or rectangles.
• I want a colour rich design with my brand colours, but it must be balanced.
• I want more modern than traditional, but simple modern
Should not have
• Not corporate
• Please don't waste my time if your not going to think about it.
• Don't mess with my primary logo
• Don't change my colours
• Don't overlay logo on image

```html
<!DOCTYPE html>
<html lang="en">
<head>
<meta charset="utf-8">
<title>Moxy Fen – Business Card</title>
<link href="https://fonts.googleapis.com/css2?family=Open+Sans:wght@400;600;700&display=swap" rel="stylesheet">
<style>
  :root {
    --brand-navy: #26376e;
    --brand-band: #3a4f8c;
    --brand-grey: #5f6368;
    --card-frost: #eceef1;
    --stage: #d9d5cf;
    --band-text: #e8ecf6;
  }
  * { margin: 0; padding: 0; box-sizing: border-box; }
  html, body {
    width: 1200px; height: 969px; overflow: hidden;
    background: var(--stage);
    font-family: "Open Sans", sans-serif;
  }
  .card {
    position: absolute; left: 90px; top: 195px;
    width: 1020px; height: 580px;
    border-radius: 28px;
    background: linear-gradient(160deg, #f3f4f6 0%, var(--card-frost) 60%, #e2e5ea 100%);
    box-shadow: 0 10px 40px rgba(0,0,0,0.12);
    overflow: hidden;
  }
  .brand-name {
    position: absolute; left: 0; right: 0; top: 118px;
    text-align: center;
    font-weight: 600; font-size: 98px; line-height: 1;
    color: var(--brand-navy); letter-spacing: -1px;
  }
  .person-name {
    position: absolute; left: 0; right: 0; top: 282px;
    text-align: center; font-weight: 600; font-size: 35px;
    color: var(--brand-navy);
  }
  .person-role {
    position: absolute; left: 0; right: 0; top: 324px;
    text-align: center; font-size: 27px; color: var(--brand-grey);
  }
  .contact-band {
    position: absolute; left: 0; right: 0; top: 394px; height: 151px;
    background: linear-gradient(90deg, var(--brand-band), #4a5f9a 50%, var(--brand-band));
  }
  .contact-list {
    position: absolute; left: 36px; top: 14px;
    list-style: none; color: var(--band-text); font-size: 26px;
  }
  .contact-list li { display: flex; align-items: center; height: 40px; }
  .contact-list svg { width: 24px; height: 24px; margin-right: 18px; fill: var(--band-text); }
  .address {
    position: absolute; right: 30px; top: 14px;
    text-align: right; color: var(--band-text); font-size: 26px; line-height: 40px;
  }
  .band-mark {
    position: absolute; left: 466px; top: 386px;
    width: 160px; height: 160px; border-radius: 50%;
    border: 6px solid rgba(232,236,246,0.8);
  }
</style>
</head>
<body>
  <section class="card">
    <h1 class="brand-name">Moxy Fen</h1>
    <p class="person-name">Dara Quillon</p>
    <p class="person-role">CEO, Professional Scrum Trainer</p>

    <div class="contact-band">
      <ul class="contact-list">
        <li>
          <svg viewBox="0 0 24 24" aria-hidden="true"><path d="M6.6 10.8a15.1 15.1 0 0 0 6.6 6.6l2.2-2.2c.3-.3.7-.4 1-.2 1.1.4 2.3.6 3.6.6.6 0 1 .4 1 1V20c0 .6-.4 1-1 1A17 17 0 0 1 3 4c0-.6.4-1 1-1h3.5c.6 0 1 .4 1 1 0 1.3.2 2.5.6 3.6.1.3 0 .7-.2 1z"/></svg>
          1300MOXYF
        </li>
        <li>
          <svg viewBox="0 0 24 24" aria-hidden="true"><path d="M7 1h10a2 2 0 0 1 2 2v18a2 2 0 0 1-2 2H7a2 2 0 0 1-2-2V3a2 2 0 0 1 2-2zm0 3v14h10V4zm5 15.2a1.2 1.2 0 1 0 0 2.4 1.2 1.2 0 0 0 0-2.4z"/></svg>
          +61 412 555 018
        </li>
        <li>
          <svg viewBox="0 0 24 24" aria-hidden="true"><path d="M2 5h20v14H2zm2 2v.5l8 5 8-5V7zm0 2.8V17h16V9.8l-8 5z"/></svg>
          dara@moxy-fen.com.au
        </li>
      </ul>
      <p class="address">PO Box 4817, Fernhollow<br>Lower, VIC 3999, Australia<br>www.moxy-fen.com.au</p>
    </div>
    <div class="band-mark" aria-hidden="true"></div>
  </section>
</body>
</html>
```